Tolvik Commercial Cleaning is lookong for a new business card design.

A fresh new design that's professional and stylish. We need a serious upgrade to our business cards. I have included pictures of our existing ones. Our clients include professional individuals and business owners. We woupdblike something professional and upbeat. Please have fun and see what you come uo with.

Target Market(s)

Property managers, business owners, facility managers and other similar professionals

Industry/Entity Type

Janitorial

Contact Information for Business Card

Name, cell, office number, email, web address

Font styles to use
Sans Serif

Colors

Designer to choose colors to be used in the design.

Requirements
Must have
• please use the green color in our logo
Nice to have
• Bar code
Should not have
• Address

```html
<!DOCTYPE html>
<html lang="en">
<head>
<meta charset="utf-8">
<title>Tolvik Commercial Cleaning – Business Card</title>
<link rel="stylesheet" href="https://fonts.googleapis.com/css2?family=Nunito:wght@700;800&family=Open+Sans:wght@400;600&display=swap">
<style>
  :root {
    --stage: #2b2b30;
    --card: #1f1f23;
    --card-deep: #151518;
    --green: #3bb75a;
    --blue: #3f73b8;
    --white: #f2f2f2;
    --grey: #6b6b72;
  }
  * { box-sizing: border-box; margin: 0; padding: 0; }
  html, body { width: 1200px; height: 780px; overflow: hidden; }
  body { background: var(--stage); position: relative; font-family: "Open Sans", Arial, sans-serif; }

  .card {
    position: absolute;
    width: 560px;
    height: 320px;
    border-radius: 22px;
    background: var(--card);
    border: 2px solid var(--green);
    overflow: hidden;
  }
  .card--back { left: 50px; top: 60px; }
  .card--front { left: 590px; top: 400px; }

  /* Back */
  .back-pattern {
    position: absolute; inset: 0;
    background: linear-gradient(200deg, #8a8a90 0%, #3a3a40 22%, var(--card-deep) 45%, var(--card) 100%);
  }
  .back-name {
    position: absolute; right: 70px; top: 118px;
    font-family: "Nunito", Arial, sans-serif;
    font-weight: 800; font-size: 40px;
    color: var(--green);
  }

  /* Front */
  .title-tab {
    position: absolute; right: 0; top: 0;
    width: 16px; height: 70px;
    background: var(--green);
  }
  .person {
    position: absolute; right: 34px; top: 26px;
    text-align: right;
    font-family: "Nunito", Arial, sans-serif;
  }
  .person__name { font-weight: 800; font-size: 26px; line-height: 1.1; }
  .person__first { color: var(--green); }
  .person__last { color: var(--blue); }
  .person__role { font-family: "Open Sans", Arial, sans-serif; font-size: 14px; color: var(--white); margin-top: 2px; }

  .brand {
    position: absolute; left: 40px; top: 104px;
    font-family: "Nunito", Arial, sans-serif;
  }
  .brand__name { font-weight: 800; font-size: 70px; line-height: 1; color: var(--green); letter-spacing: -1px; }
  .brand__tagline { font-weight: 700; font-size: 17px; color: var(--blue); margin-top: 4px; letter-spacing: .3px; }

  .contacts {
    position: absolute; left: 40px; bottom: 26px;
    list-style: none;
  }
  .contacts li {
    display: flex; align-items: center; gap: 10px;
    font-size: 14px; color: var(--white); line-height: 24px;
  }
  .contacts svg { width: 15px; height: 15px; flex: none; }
</style>
</head>
<body>

  <section class="card card--back" aria-label="Card back">
    <div class="back-pattern" role="img" aria-label="Repeating brand pattern fading from silver to black"></div>
    <div class="back-name">Tolvik</div>
  </section>

  <section class="card card--front" aria-label="Card front">
    <div class="title-tab"></div>
    <div class="person">
      <div class="person__name"><span class="person__first">Maren</span> <span class="person__last">Ostby</span></div>
      <div class="person__role">Director</div>
    </div>

    <div class="brand">
      <div class="brand__name">Tolvik</div>
      <div class="brand__tagline">commercial cleaning</div>
    </div>

    <ul class="contacts">
      <li>
        <svg viewBox="0 0 24 24" aria-hidden="true"><path fill="var(--green)" d="M6.6 10.8a15.1 15.1 0 0 0 6.6 6.6l2.2-2.2c.3-.3.7-.4 1-.2 1.1.4 2.3.6 3.6.6.6 0 1 .4 1 1V20c0 .6-.4 1-1 1A17 17 0 0 1 3 4c0-.6.4-1 1-1h3.5c.6 0 1 .4 1 1 0 1.3.2 2.5.6 3.6.1.3 0 .7-.2 1z"/></svg>
        (555) 014-2293
      </li>
      <li>
        <svg viewBox="0 0 24 24" aria-hidden="true"><rect x="2" y="5" width="20" height="14" rx="2" fill="var(--green)"/><path d="M3 6l9 7 9-7" fill="none" stroke="var(--card)" stroke-width="2"/></svg>
        maren@tolvikcleaning.com
      </li>
      <li>
        <svg viewBox="0 0 24 24" aria-hidden="true"><circle cx="12" cy="12" r="10" fill="var(--green)"/><path d="M2 12h20M12 2c3 3 3 17 0 20M12 2c-3 3-3 17 0 20" fill="none" stroke="var(--card)" stroke-width="1.5"/></svg>
        www.tolvikcleaning.com
      </li>
    </ul>
  </section>

</body>
</html>
```